Restyle corporate identity (+ logo) for a road construction company

We need a new logo and stationary design for our company VARNOK path. VARNOK path® increases the road base strength, while reducing major costs and time of road construction. Attached some examples of the current design.

Our wishes for the new logo:
- Business look
- Style sheet
- Modern

More information: www.varnokpath.example
Updates

Target Market(s)

Government

Industry/Entity Type

Construction

Requirements
Must have
• Logo (with road sign) + text

```html
<!DOCTYPE html>
<html lang="en">
<head>
<meta charset="utf-8">
<title>VARNOK path – Business Card</title>
<link rel="stylesheet" href="https://fonts.googleapis.com/css2?family=Open+Sans:wght@400;600;700&display=swap">
<style>
  :root {
    --bg: #8f9193;
    --card-white: #eff0f0;
    --brand-blue: #1c7fe2;
    --text-dark: #3f4245;
    --text-mid: #6b6e71;
    --text-light: #f2f7fd;
  }
  * { box-sizing: border-box; margin: 0; padding: 0; }
  html, body { width: 1105px; height: 1200px; overflow: hidden; }
  body {
    background: var(--bg);
    font-family: "Open Sans", Arial, sans-serif;
    position: relative;
  }
  .card {
    position: absolute;
    left: 182px;
    width: 747px;
    height: 427px;
    box-shadow: 0 8px 18px rgba(0,0,0,.25);
  }
  .card--front { top: 119px; background: var(--card-white); }
  .card--back { top: 636px; background: var(--brand-blue); }

  .wordmark {
    display: flex;
    align-items: center;
    gap: 14px;
    font-weight: 700;
    line-height: 1;
    letter-spacing: 2px;
  }
  .wordmark__square { width: 44px; height: 44px; background: currentColor; }
  .wordmark__text { display: flex; flex-direction: column; gap: 6px; font-size: 40px; }

  .card--front .wordmark { position: absolute; left: 52px; top: 58px; color: var(--brand-blue); }
  .divider {
    position: absolute; left: 52px; top: 162px;
    width: 649px; height: 2px; background: var(--brand-blue);
  }
  .holder { position: absolute; right: 46px; top: 90px; text-align: right; }
  .holder__name { color: var(--brand-blue); font-weight: 600; font-size: 25px; letter-spacing: .5px; }
  .holder__role { color: var(--text-mid); font-size: 19px; margin-top: 2px; }
  .edge-tab {
    position: absolute; right: 0; top: 95px;
    width: 14px; height: 53px; background: var(--brand-blue);
  }
  .contacts { position: absolute; left: 52px; top: 298px; list-style: none; }
  .contacts li {
    display: flex; align-items: center; gap: 10px;
    height: 28.5px; font-size: 19px; color: var(--text-dark);
  }
  .contacts svg { width: 18px; height: 18px; fill: var(--brand-blue); }
  .address {
    position: absolute; right: 46px; top: 298px;
    text-align: right; font-style: normal;
    font-size: 19px; line-height: 28.5px; color: var(--text-dark);
  }

  .card--back .wordmark {
    position: absolute; left: 50%; top: 212px;
    transform: translate(-50%, -50%); color: var(--text-light);
  }
  .card--back .wordmark__text { font-size: 46px; }
  .card--back .wordmark__square { width: 52px; height: 52px; }
  .back-web {
    position: absolute; left: 0; right: 0; top: 357px;
    text-align: center; color: var(--text-light);
    font-size: 19px; letter-spacing: 4px;
  }
</style>
</head>
<body>
  <section class="card card--front">
    <div class="wordmark">
      <span class="wordmark__square"></span>
      <span class="wordmark__text"><span>VARNOK</span><span>PATH</span></span>
    </div>
    <div class="holder">
      <p class="holder__name">MAREK LINDQVIST</p>
      <p class="holder__role">CEO/Founder</p>
    </div>
    <span class="edge-tab"></span>
    <div class="divider"></div>
    <ul class="contacts">
      <li><svg viewBox="0 0 24 24"><path d="M6.6 10.8a15.2 15.2 0 0 0 6.6 6.6l2.2-2.2a1 1 0 0 1 1-.25 11.4 11.4 0 0 0 3.6.57 1 1 0 0 1 1 1V20a1 1 0 0 1-1 1A17 17 0 0 1 3 4a1 1 0 0 1 1-1h3.5a1 1 0 0 1 1 1c0 1.25.2 2.45.57 3.57a1 1 0 0 1-.25 1z"/></svg>555 210 4786</li>
      <li><svg viewBox="0 0 24 24"><path d="M2 5h20v14H2z M2 5l10 8 10-8" fill="none" stroke="#1c7fe2" stroke-width="0"/><path d="M2 6.5V19h20V6.5l-10 7.5z M2.5 5h19L12 12.2z"/></svg>marek@varnokpath.example</li>
      <li><svg viewBox="0 0 24 24"><circle cx="12" cy="12" r="10"/><path d="M2 12h20M12 2c3 3 3 17 0 20M12 2c-3 3-3 17 0 20" fill="none" stroke="#eff0f0" stroke-width="1.4"/></svg>www.varnokpath.example</li>
    </ul>
    <address class="address">
      Ostrander Kade 57<br>
      4127 VL Marrenburg<br>
      The Netherlands
    </address>
  </section>

  <section class="card card--back">
    <div class="wordmark">
      <span class="wordmark__square"></span>
      <span class="wordmark__text"><span>VARNOK</span><span>PATH</span></span>
    </div>
    <p class="back-web">www.varnokpath.example</p>
  </section>
</body>
</html>
```